NZ First of it's kind solutions directory and marketplace for busy Mums needs a business card design

We need a business card design for our new nationwide business in NZ (long term plans to go global). We provide solutions to the everyday challenges that busy Mums face by connecting them with quality communities and suppliers of carefully selected, relevant products and services. We sell direct via our online marketplace. The final design should communicate our values of inclusivity, quality and smart solutions. Colours should incorporate our logo colour palette of #477077 and #6ba8b2. Our website is at https://www.brightnestmums.example

Target Market(s)

busy Mums, Age 28 – 50, female, income over $100K, location main centres NZ primarily but NZ wide. Is likely juggling work or career with a young family. Probably had hobbies which have fallen by the wayside.
-Wants to succeed in her chosen career without compromising on family life
-to successfully juggle her career without feeling like she is compromising her children
- Is time poor, something always has to give and it’s generally her health (she’ll stay up late, get stressed)
- probably ex corporate or professional career. Has discretional income

Industry/Entity Type

Business

Contact Information for Business Card

Lena Forbisher, Founder, BrightNestMums.example (Strapline Tap; Gather; Sorted), 47 Kowhai Terrace, Ellerslie, Auckland 1051, New Zealand. Mob: 021 483 517 Ph: +64 (0)9 571 4860

Font styles to use
Other font styles liked:
• Raleway, and/or Architects Daughter

Colors
00a990
33b8a4
86cfc6
cfeae6

Requirements
Must have
• the above details, streamline. the logo and colours associated with those logos
Should not have
• foil or metallic colours

```html
<!DOCTYPE html>
<html lang="en">
<head>
<meta charset="utf-8">
<title>BrightNestMums Business Card</title>
<link rel="stylesheet" href="https://fonts.googleapis.com/css2?family=Arimo:wght@400;700&family=Open+Sans:wght@600;700&display=swap">
<style>
  :root {
    --stage: #000000;
    --card-front: #f3f3f3;
    --card-back: #ffffff;
    --teal-dark: #477077;
    --teal-light: #6ba8b2;
    --ink: #333333;
    --ink-name: #444444;
  }
  html, body {
    margin: 0;
    padding: 0;
    width: 1200px;
    height: 900px;
    overflow: hidden;
    background: var(--stage);
  }
  .stage {
    position: relative;
    width: 1200px;
    height: 900px;
    background: var(--stage);
    font-family: "Arimo", Arial, sans-serif;
  }
  .card {
    position: absolute;
    top: 200px;
    width: 310px;
    height: 502px;
    overflow: hidden;
  }
  .card--front {
    left: 265px;
    background: var(--card-front);
    border-radius: 52px 0 72px 0;
  }
  .card--back {
    left: 641px;
    width: 309px;
    background: var(--card-back);
    border-radius: 0 56px 0 60px;
  }
  .brand {
    position: absolute;
    left: 30px;
    top: 146px;
    display: flex;
    align-items: center;
    gap: 10px;
  }
  .brand__dot {
    width: 30px;
    height: 30px;
    border-radius: 50%;
    background: var(--teal-dark);
  }
  .brand__name {
    font-weight: 700;
    font-size: 26px;
    letter-spacing: -0.5px;
    color: var(--teal-dark);
  }
  .person {
    position: absolute;
    left: 27px;
    top: 314px;
  }
  .person__name {
    margin: 0;
    font-size: 18px;
    font-weight: 700;
    color: var(--ink-name);
    text-transform: uppercase;
    letter-spacing: 0.2px;
  }
  .person__first { color: var(--teal-dark); }
  .person__role {
    margin: 1px 0 0;
    font-size: 14px;
    color: var(--ink);
  }
  .contact {
    position: absolute;
    left: 28px;
    top: 364px;
    margin: 0;
    padding: 0;
    list-style: none;
    font-size: 14px;
    line-height: 18px;
    color: var(--ink);
  }
  .contact li {
    display: flex;
    align-items: center;
    gap: 5px;
  }
  .contact svg { width: 11px; height: 11px; fill: var(--teal-dark); flex: none; }
  .address {
    position: absolute;
    left: 28px;
    top: 428px;
    margin: 0;
    font-style: normal;
    font-size: 14px;
    line-height: 18px;
    color: var(--ink);
  }
  .emblem {
    position: absolute;
    left: 80px;
    top: 200px;
    width: 148px;
    height: 148px;
    border-radius: 50%;
    background: var(--teal-dark);
  }
  .back-url {
    position: absolute;
    left: 0;
    right: 0;
    top: 447px;
    text-align: center;
    font-family: "Open Sans", Arial, sans-serif;
    font-weight: 700;
    font-size: 15px;
    letter-spacing: 0.8px;
    color: var(--teal-dark);
  }
</style>
</head>
<body>
<main class="stage">
  <section class="card card--front" aria-label="Card front">
    <div class="brand">
      <span class="brand__dot"></span>
      <span class="brand__name">BrightNestMums</span>
    </div>
    <div class="person">
      <h1 class="person__name"><span class="person__first">Lena</span> Forbisher</h1>
      <p class="person__role">Founder</p>
    </div>
    <ul class="contact">
      <li>
        <svg viewBox="0 0 12 12" aria-hidden="true"><path d="M1 4c0-2 2-3 5-3s5 1 5 3v1H8.5V3.8h-5V5H1zM3 6h6l1.5 5h-9z"/></svg>
        021 483 517
      </li>
      <li>
        <svg viewBox="0 0 12 12" aria-hidden="true"><path d="M3 0h6a1 1 0 0 1 1 1v10a1 1 0 0 1-1 1H3a1 1 0 0 1-1-1V1a1 1 0 0 1 1-1zm.5 1.5v8h5v-8zM6 10.2a.6.6 0 1 0 0 1.2.6.6 0 0 0 0-1.2z"/></svg>
        +64 (0)9 571 4860
      </li>
      <li>
        <svg viewBox="0 0 12 12" aria-hidden="true"><circle cx="6" cy="6" r="5.5"/></svg>
        www.BrightNestMums.example
      </li>
    </ul>
    <address class="address">
      47 Kowhai Terrace, Ellerslie<br>
      Auckland 1051, New Zealand
    </address>
  </section>

  <section class="card card--back" aria-label="Card back">
    <div class="emblem"></div>
    <div class="back-url">www.BrightNestMums.example</div>
  </section>
</main>
</body>
</html>
```